Marwick Law Letterhead

We need a new letterhead design for a Law Firm. The address for the law firm is 1475 Calloway Street, Suite 210, Houston, Texas 77041. Phone Number: 832-361-9027; Fax Number: 832-614-7359. The logo is uploaded to the project.

```html
<!DOCTYPE html>
<html lang="en">
<head>
<meta charset="utf-8">
<title>Marwick Law Letterhead</title>
<link rel="stylesheet" href="https://fonts.googleapis.com/css2?family=Montserrat:wght@400;500;600&display=swap">
<style>
  :root {
    --backdrop: #e9e9ea;
    --paper: #ffffff;
    --navy: #142a5c;
    --red: #e31e2b;
    --ink: #2b2b2b;
    --muted: #555555;
  }
  * { box-sizing: border-box; margin: 0; padding: 0; }
  html, body {
    width: 1200px; height: 874px; overflow: hidden;
    background: var(--backdrop);
    font-family: "Montserrat", Arial, sans-serif;
  }
  .letterhead {
    position: absolute; left: 300px; top: 13px;
    width: 600px; height: 848px;
    background: var(--paper);
    box-shadow: 0 6px 24px rgba(0,0,0,0.12);
    overflow: hidden;
    color: var(--ink);
  }
  .contact {
    position: absolute; right: 40px; top: 44px;
    font-size: 10px; line-height: 15px; text-align: right;
  }
  .contact-line { display: flex; align-items: center; justify-content: flex-end; gap: 6px; }
  .contact-icon { width: 11px; height: 11px; background: var(--red); border-radius: 2px; display: inline-flex; align-items: center; justify-content: center; }
  .brand {
    position: absolute; left: 44px; top: 96px;
    display: flex; align-items: center; gap: 12px;
  }
  .brand-mark { width: 34px; height: 34px; background: var(--navy); }
  .brand-name { font-size: 26px; font-weight: 600; color: var(--navy); letter-spacing: 0.5px; }
  .recipient {
    position: absolute; left: 60px; top: 218px;
    font-size: 11px; line-height: 16px;
  }
  .letter-body {
    position: absolute; left: 60px; top: 300px; width: 480px;
    font-size: 10.5px; line-height: 16px; color: var(--ink);
  }
  .letter-body p { margin-bottom: 16px; }
  .closing { margin-top: 4px; font-size: 10.5px; }
  .signature {
    width: 150px; height: 48px; margin-top: 8px;
    background: linear-gradient(90deg, #f1f1f1, #e2e2e2);
  }
  .footer-band { position: absolute; left: 0; bottom: 0; width: 600px; height: 120px; }
  .footer-address {
    position: absolute; left: 56px; bottom: 22px;
    color: #fff; font-size: 11px; font-weight: 500;
    display: flex; align-items: center; gap: 7px;
    transform: rotate(-7deg); transform-origin: left bottom;
  }
</style>
</head>
<body>
  <main class="letterhead">
    <div class="contact">
      <div class="contact-line">832-361-9027
        <span class="contact-icon"><svg width="7" height="7" viewBox="0 0 10 10"><path d="M2 1l2 2-1 1.5c.6 1.2 1.3 1.9 2.5 2.5L7 6l2 2-1.2 1.5C4.5 9 1 5.5.5 2.2z" fill="#fff"/></svg></span>
      </div>
      <div class="contact-line">832-614-7359
        <span class="contact-icon"><svg width="7" height="7" viewBox="0 0 10 10"><rect x="2" y="0.5" width="6" height="3" fill="#fff"/><rect x="0.5" y="4" width="9" height="4" fill="#fff"/><rect x="2" y="7" width="6" height="2.5" fill="#fff"/></svg></span>
      </div>
    </div>

    <header class="brand">
      <span class="brand-mark"></span>
      <span class="brand-name">Marwick Law</span>
    </header>

    <section class="recipient">
      <div>Mr/s</div>
      <div>First Name and Last Name</div>
      <div>Company Name</div>
      <div>Address</div>
    </section>

    <section class="letter-body">
      <p>Lorem Ipsum is simply dummy text of the printing and typesetting industry. Lorem Ipsum has been the industry's standard dummy text ever since the 1500s, when an unknown printer took a galley of type and scrambled it to make a type specimen book. It has survived not only five centuries, but also the leap into electronic typesetting, remaining essentially unchanged. It was popularised in the 1960s with the release of Letraset sheets containing Lorem Ipsum passages.</p>
      <p>The standard chunk of Lorem Ipsum used since the 1500s is reproduced below for those interested. Sections 1.10.32 and 1.10.33 from "de Finibus Bonorum et Malorum" by Cicero are also reproduced in their exact original form, accompanied by English versions from the 1914 translation by H. Rackham. Lorem ipsum dolor sit amet, consectetur adipiscing elit, sed do eiusmod tempor incididunt ut labore et dolore magna aliqua.</p>
      <p>It is a long established fact that a reader will be distracted by the readable content of a page when looking at its layout. The point of using Lorem Ipsum is that it has a more-or-less normal distribution of letters, as opposed to using 'Content here, content here', making it look like readable English. Many desktop publishing packages and web page editors now.</p>
      <div class="closing">Your Sincerely,</div>
      <div class="signature" role="img" aria-label="Handwritten signature"></div>
    </section>

    <svg class="footer-band" viewBox="0 0 600 120" preserveAspectRatio="none" aria-hidden="true">
      <path d="M0 120 C 160 40, 380 20, 600 18 L600 120 Z" fill="var(--red)"/>
      <path d="M0 120 C 170 50, 390 30, 600 26 L600 120 Z" fill="var(--navy)"/>
    </svg>
    <div class="footer-address">
      <svg width="9" height="12" viewBox="0 0 10 14"><path d="M5 0a5 5 0 0 0-5 5c0 3.5 5 9 5 9s5-5.5 5-9a5 5 0 0 0-5-5zm0 7a2 2 0 1 1 0-4 2 2 0 0 1 0 4z" fill="#fff"/></svg>
      1475 Calloway Street, Suite 210, Houston, Texas 77041
    </div>
  </main>
</body>
</html>
```